Craft beer label required for new modern craft brewery

I require a label to be designed for my craft beer, the name of the beer is "Lanternfish Pale Ale".
It has to be a contemporary style label targeting an audience group between the ages of 21-40. It must be unique and appealing.
The label must incorporate the image of a Gladiator which has to originally created (I’m giving you creative freedom), not copied (for copy right reasons). I’m attaching a few examples, please refer to “gladiator1.jpg” and “Gladiator2.jpg”.
It would be nice if the Coliseum could appear in the background, also originally created I’m attaching an example, please refer to “Coliseum1.jpg”
The Label must also incorporate the attached logo “Copperwell Brewing Co. Craft Beer-01.jpg” .
The label must fit a 440ml bottle
Please use creative freedom with regards to the shape of the label.
The colours do not have to be exactly the same as logo, but obviously they must match.
Updates

Project Deadline Extended Reason: Not 100% happy with the submissions, almost there.I'd also like to give those designers, that haven't submitted, a chance to submit. Added Tuesday, September 26, 2017

Target Market(s)

Modern/contemporary successful 21-40 year olds

Industry/Entity Type

Brewery

Font styles to use
Serif
Script

Colors

Designer to choose colors to be used in the design.

Requirements
Must have
• My logo, the beer name and the image of a gladiator
• The label size should be at least 10cm wide x 9cm wide.
• The label must include the size of the bottle: 440ml
• The label must include 6.5% ALC./VOL.
Nice to have
• Coliseum in the back ground
Should not have
• Copied images or trade marks

```html
<!DOCTYPE html>
<html lang="en">
<head>
<meta charset="utf-8">
<title>Lanternfish Pale Ale – Label</title>
<link rel="stylesheet" href="https://fonts.googleapis.com/css2?family=Pacifico&family=Cinzel:wght@700&family=Oswald:wght@500&display=swap">
<style>
  :root {
    --backdrop: #e9eced;
    --label-black: #111214;
    --crimson: #c8203a;
    --crimson-dark: #8e1628;
    --gold: #c9a45a;
    --teal-light: #bdeee9;
    --white: #ffffff;
  }
  html, body {
    margin: 0;
    width: 1200px;
    height: 901px;
    overflow: hidden;
    background: var(--backdrop);
  }
  .label-canvas { display: block; width: 1200px; height: 901px; }
  .label-body { fill: var(--label-black); }
  .label-wing { fill: var(--crimson); }
  .brand-seal { fill: var(--label-black); }
  .brand-ring { fill: none; stroke: var(--gold); stroke-width: 2; }
  .brand-name {
    font-family: "Oswald", sans-serif;
    font-weight: 500;
    font-size: 16px;
    letter-spacing: 2px;
    fill: var(--gold);
    text-anchor: middle;
  }
  .beer-name {
    font-family: "Pacifico", cursive;
    font-size: 68px;
    fill: var(--crimson);
    stroke: var(--white);
    stroke-width: 3px;
    paint-order: stroke;
    text-anchor: middle;
  }
  .beer-style {
    font-family: "Cinzel", serif;
    font-weight: 700;
    font-size: 36px;
    fill: var(--teal-light);
    letter-spacing: 2px;
    text-anchor: middle;
  }
  .content-banner { fill: var(--crimson); }
  .banner-fold { fill: var(--crimson-dark); }
  .banner-text {
    font-family: "Oswald", sans-serif;
    font-weight: 500;
    font-size: 21px;
    fill: var(--white);
    letter-spacing: 1px;
    text-anchor: middle;
  }
</style>
</head>
<body>
<svg class="label-canvas" viewBox="0 0 1200 901" xmlns="http://www.w3.org/2000/svg">
  <defs>
    <linearGradient id="arena-sky" x1="0" y1="0" x2="0" y2="1">
      <stop offset="0" stop-color="#5fd0c8"/>
      <stop offset="0.35" stop-color="#9fd8cf"/>
      <stop offset="0.6" stop-color="#c9b89a"/>
      <stop offset="1" stop-color="#a88f72"/>
    </linearGradient>
    <radialGradient id="arena-hero" cx="0.62" cy="0.7" r="0.6">
      <stop offset="0" stop-color="#2a4f8a" stop-opacity="0.95"/>
      <stop offset="0.45" stop-color="#3468a8" stop-opacity="0.75"/>
      <stop offset="0.75" stop-color="#d98a4a" stop-opacity="0.25"/>
      <stop offset="1" stop-color="#d98a4a" stop-opacity="0"/>
    </radialGradient>
    <clipPath id="arena-window">
      <path d="M395 760 L395 470 Q395 410 455 410 L745 410 Q805 410 805 470 L805 760 Z"/>
    </clipPath>
  </defs>

  <!-- side wings -->
  <polygon class="label-wing" points="372,430 330,470 330,700 372,740"/>
  <polygon class="label-wing" points="828,430 870,470 870,700 828,740"/>

  <!-- label body -->
  <path class="label-body" d="M372 220 L828 220 L828 760 L372 760 Z"/>

  <!-- brand seal -->
  <circle class="brand-seal" cx="600" cy="190" r="92"/>
  <circle class="brand-ring" cx="600" cy="150" r="14"/>
  <text class="brand-name" x="600" y="194">COPPERWELL</text>
  <text class="brand-name" x="600" y="216">BREWING CO.</text>

  <!-- beer name -->
  <text class="beer-name" x="600" y="334">Lanternfish</text>
  <text class="beer-style" x="600" y="394">PALE ALE</text>

  <!-- illustration area -->
  <g role="img" aria-label="Illustration of a horned gladiator reaching forward in front of the Colosseum, teal sky, stone arena and blue armour" clip-path="url(#arena-window)">
    <rect x="395" y="410" width="410" height="350" fill="url(#arena-sky)"/>
    <rect x="395" y="410" width="410" height="350" fill="url(#arena-hero)"/>
  </g>

  <!-- content banner -->
  <polygon class="banner-fold" points="380,712 352,728 380,744"/>
  <polygon class="banner-fold" points="820,712 848,728 820,744"/>
  <path class="content-banner" d="M372 705 Q600 745 828 705 L820 775 Q600 812 380 775 Z"/>
  <text class="banner-text" x="600" y="769">NET CONTENTS 440ml · 6.5% ALC./VOL.</text>
</svg>
</body>
</html>
```